Summit Bodyform Gym Website

We need a website design for our gym.

Summit is the UAE's first calisthenics and parkour gym. The theme under which the gym revolves is that one does not require any machinery to workout as our bodies could be themselves the machinery. The gym is designed to be the more of a social hub rather than an "in-and-out" gym, where people come train, have fun, hang out and socialize for a few hours rather than just train for 60 minutes then leave. The gym is designed to be a big open space with lots of natural sunlight, natural wood and plants all over the place to create a natural and refreshing setting. We also use recycled material throughout the gym and recycle our waste as being green is part of our philosophy. We currently also have some of the world's top and most recognized calisthenics athletes working with us.

We would like our website to reflect all that as well as provide a simple, interactive and fun way for visitors to be able to get class and gym information, check out gym media and contact us for bookings.

Target Market(s)

Ages 15-35

Industry/Entity Type

Fitness

Coding

Coded - Design and coding required

Number of Pages Required

4 page

Font styles to use
Decorative

Colors
0792cd

Requirements
Must have
• Class descriptions
• Gym description
• Class schedules
• Trainer profiles
• Gym philosophy
• Contact Details
Nice to have
• A link to contact us directly for a free first trial class

```html
<!DOCTYPE html>
<html lang="en">
<head>
<meta charset="utf-8">
<title>Summit Bodyform Gym</title>
<link href="https://fonts.googleapis.com/css2?family=Roboto:wght@300;400;500;700&family=Roboto+Condensed:wght@400;700&display=swap" rel="stylesheet">
<style>
:root{
  --brand:#0792cd;
  --brand-dark:#0a7fb0;
  --ink:#222;
  --text:#666;
  --muted:#888;
  --nav:#1f1f20;
  --panel:#f1f1f1;
  --footer:#1d1d1e;
  --white:#fff;
}
*{box-sizing:border-box;margin:0;padding:0}
html,body{width:1200px;height:2899px;overflow:hidden}
body{position:relative;background:var(--white);font-family:'Roboto',sans-serif;color:var(--text)}
.abs{position:absolute}
a{color:inherit;text-decoration:none}

/* header */
.site-header{left:0;top:0;width:1200px;height:143px;background:var(--white)}
.brand{left:100px;top:28px;display:flex;align-items:center;gap:12px}
.brand-dot{width:34px;height:34px;border-radius:50%;background:var(--brand)}
.brand-name{font-weight:700;font-size:34px;color:var(--ink);line-height:1}
.brand-tag{left:146px;top:72px;font-size:13px;color:var(--ink)}
.top-links{left:578px;top:21px;display:flex;gap:34px;font-size:12px;color:var(--muted)}
.top-links span{display:flex;align-items:center;gap:6px}
.top-links svg{width:11px;height:11px;fill:var(--brand)}
.search{left:835px;top:70px;width:264px;height:38px;display:flex}
.search-field{flex:1;border:1px solid #ddd;font-size:12px;color:#aaa;padding:11px 12px}
.search-btn{width:41px;background:#333;display:flex;align-items:center;justify-content:center}

/* nav */
.main-nav{left:0;top:143px;width:1200px;height:66px;background:var(--nav)}
.main-nav ul{list-style:none;position:absolute;left:108px;top:0;height:66px;display:flex}
.main-nav li{font-size:12.5px;font-weight:700;color:var(--white);text-transform:uppercase;line-height:66px;margin-right:46px;position:relative}
.main-nav li.active{color:var(--brand)}
.main-nav li.active::after{content:"";position:absolute;left:-8px;right:-8px;bottom:0;height:4px;background:var(--brand)}

/* hero */
.hero{left:0;top:209px;width:1200px;height:595px;background:#000}
.hero-photo{left:0;top:0;width:1200px;height:595px;background:radial-gradient(ellipse 380px 420px at 630px 300px,#4a3630 0%,#1c1412 45%,#000 80%)}
.hero-arrow{top:208px;width:32px;height:32px;border:2px solid #bbb;border-radius:50%;display:flex;align-items:center;justify-content:center}
.hero-title{left:98px;top:360px;font-family:'Roboto Condensed',sans-serif;font-size:92px;letter-spacing:15px;color:var(--brand);line-height:1}
.hero-sub{left:100px;top:466px;font-family:'Roboto Condensed',sans-serif;font-weight:700;font-size:26px;color:var(--white)}

/* intro blocks */
.photo-bars{left:0;top:804px;width:622px;height:346px;background:linear-gradient(135deg,#2b2f33,#4d5852 50%,#2a2f2b)}
.welcome{left:622px;top:769px;width:578px;height:423px;background:var(--white)}
.section-head{display:flex;align-items:center;gap:12px}
.section-mark{width:32px;height:32px;border-radius:50%;background:var(--brand)}
.section-head h2{font-size:25px;font-weight:500;color:var(--ink)}
.copy{font-size:12px;line-height:22px;color:var(--text);text-align:justify}
.copy-tight{font-size:11px;line-height:21px}
.btn{display:flex;align-items:center;justify-content:center;background:var(--brand);color:var(--white);font-weight:700;font-size:13px;text-transform:uppercase;border-radius:5px}
.gym-desc{left:0;top:1150px;width:589px;height:315px;background:var(--panel)}
.photo-hall{left:589px;top:1192px;width:611px;height:273px;background:linear-gradient(180deg,#e6e6e6,#b9bcbc 55%,#7d7f80)}

/* video */
.thumb{border:4px solid var(--white);box-shadow:0 1px 4px rgba(0,0,0,.25)}
.t1{left:100px;top:1524px;width:226px;height:147px;background:linear-gradient(#b9c3c8,#7c6f60)}
.t2{left:379px;top:1513px;width:241px;height:106px;background:linear-gradient(#e4e0dc,#c7b6a4)}
.t3{left:104px;top:1714px;width:275px;height:166px;background:linear-gradient(#f0f0f0,#d6cfc8)}
.t4{left:404px;top:1795px;width:218px;height:104px;background:linear-gradient(#dcdcdc,#b6b0a6)}
.t-main{left:222px;top:1590px;width:358px;height:212px;background:linear-gradient(135deg,#b23a2a,#3a5b2e 60%,#21301c);z-index:2}
.play{left:378px;top:1645px;width:64px;height:64px;border-radius:50%;background:rgba(255,255,255,.55);z-index:3;display:flex;align-items:center;justify-content:center}

/* workout band */
.workout{left:0;top:1946px;width:1200px;height:537px;background:radial-gradient(ellipse 600px 400px at 500px 250px,#214a58,#0f2630 60%,#0a1a22)}
.workout-photo{left:820px;top:0;width:380px;height:537px;background:linear-gradient(90deg,rgba(10,26,34,0),#6b5a4e 55%,#3d4538)}
.workout .section-head h2{color:var(--white)}
.workout-lead{left:100px;top:152px;width:660px;font-size:13px;line-height:23px;color:#2aa9e0}
.feature{width:340px}
.feature h3{font-size:18px;font-weight:500;color:var(--white);margin-bottom:8px}
.feature p{font-size:11.5px;line-height:20px;color:#e2e8ea;width:270px}
.feature-icon{width:46px;height:46px}
.feature-icon svg{width:46px;height:46px;stroke:#e8eef0;fill:none;stroke-width:2}

/* cta */
.cta-title{left:100px;top:2523px;font-size:17px;font-weight:700;color:var(--ink)}
.cta-copy{left:100px;top:2554px;width:680px;font-size:11.5px;line-height:21px;color:var(--text)}
.cta-btn{left:867px;top:2523px;width:232px;height:72px;background:var(--brand);border-radius:6px;color:var(--white);text-align:center;padding-top:14px}
.cta-btn strong{display:block;font-size:20px;font-weight:700;letter-spacing:.5px}
.cta-btn span{display:block;font-size:11px;color:#0d3e54;font-weight:500;margin-top:4px}

/* footer */
.site-footer{left:0;top:2639px;width:1200px;height:260px;background:var(--footer);color:var(--white)}
.foot-head{font-size:13px;font-weight:700;text-transform:uppercase}
.foot-list{list-style:none;font-size:11.5px;line-height:21px;font-weight:500}
.foot-contact li{display:flex;align-items:center;gap:10px}
.foot-contact svg{width:14px;height:14px;fill:var(--white)}
.socials{display:flex;gap:13px}
.socials span{width:22px;height:22px;background:var(--brand);border-radius:2px}
.about-copy{font-size:11px;line-height:18px;width:400px}
.newsletter{left:680px;top:151px;width:419px;height:39px;display:flex}
.newsletter-field{flex:1;background:var(--white);color:#aaa;font-size:11px;font-style:italic;padding:12px 14px}
.newsletter-btn{width:98px;background:var(--brand);font-size:12px;font-weight:700;display:flex;align-items:center;justify-content:center;text-transform:uppercase}
.copyright{left:100px;top:224px;font-size:11px;color:#aaa}
</style>
</head>
<body>

<header class="site-header abs">
  <div class="brand abs"><span class="brand-dot"></span><span class="brand-name">Summit.</span></div>
  <div class="brand-tag abs">calisthenics gym</div>
  <div class="top-links abs">
    <span><svg viewBox="0 0 12 12"><path d="M2 1l2 0 1 3-1.5 1a7 7 0 003.5 3.5L8 7l3 1v2c0 1-1 1.5-2 1.5A9 9 0 01.5 3C.5 2 1 1 2 1z"/></svg>+000 555 0142</span>
    <span><svg viewBox="0 0 12 12"><path d="M6 0a4 4 0 014 4c0 3-4 8-4 8S2 7 2 4a4 4 0 014-4zm0 2.5a1.5 1.5 0 100 3 1.5 1.5 0 000-3z"/></svg>Training Locations</span>
    <span><svg viewBox="0 0 12 12"><path d="M1 2h10v9H1zM2 5h8v5H2zM3 0h1.5v3H3zM7.5 0H9v3H7.5z" fill-rule="evenodd"/></svg>Training Calendar</span>
    <span><svg viewBox="0 0 12 12"><circle cx="6" cy="3.5" r="3"/><path d="M0 12c0-4 3-5 6-5s6 1 6 5z"/></svg>login &nbsp;/&nbsp; register</span>
  </div>
  <div class="search abs">
    <div class="search-field">Search...</div>
    <div class="search-btn"><svg width="16" height="16" viewBox="0 0 16 16" fill="none" stroke="#fff" stroke-width="2.4"><circle cx="6.5" cy="6.5" r="5"/><path d="M10 10l5 5"/></svg></div>
  </div>
</header>

<nav class="main-nav abs">
  <ul>
    <li class="active">Home</li>
    <li>Class Descriptions</li>
    <li>Gym Description</li>
    <li>Class Schedules</li>
    <li>Trainer Profiles</li>
    <li>Gym Philosophy</li>
    <li>Contact</li>
  </ul>
</nav>

<section class="hero abs">
  <div class="hero-photo abs" role="img" aria-label="Athlete seen from behind with arms spread wide against a black background"></div>
  <div class="hero-arrow abs" style="left:61px"><svg width="14" height="14" viewBox="0 0 14 14" fill="none" stroke="#ccc" stroke-width="2"><path d="M12 7H2M6 3L2 7l4 4"/></svg></div>
  <div class="hero-arrow abs" style="left:1105px"><svg width="14" height="14" viewBox="0 0 14 14" fill="none" stroke="#ccc" stroke-width="2"><path d="M2 7h10M8 3l4 4-4 4"/></svg></div>
  <div class="hero-title abs">SUMMIT</div>
  <div class="hero-sub abs">CALISTHENICS AND PARKOUR GYM</div>
</section>

<div class="photo-bars abs" role="img" aria-label="Athlete training on pull-up bars inside the gym"></div>

<section class="welcome abs">
  <div class="section-head abs" style="left:35px;top:36px"><span class="section-mark"></span><h2>Welcome to Summit</h2></div>
  <div class="abs" style="left:35px;top:100px;width:444px">
    <p class="copy copy-tight" style="margin-bottom:12px">There are many variations of passages of Lorem Ipsum in available, but the majority have suffered alteration in some form, by injected humour, or</p>
    <p class="copy copy-tight">Randomised words which don't look even slightly believable. If you are going to use a passage of Lorem Ipsum, you need to be sure there isn't anything embarrassing hidden in the middle of text. All the Lorem Ipsum generators on the Internet tend the to repeat predefined chunks as in necessary, making this the first true generator on the Internet. It uses a dictionary of over 200 Latin the words, combined with a handful of model sentence structures, to generate Lorem Ipsum which looks reasonable. The generated Lorem Ipsum is therefore always free from repetition, injected humour, non-characteristic.</p>
  </div>
  <a class="btn abs" style="left:35px;top:338px;width:230px;height:48px">Free First Trial Class</a>
</section>

<section class="gym-desc abs">
  <div class="section-head abs" style="left:100px;top:30px"><span class="section-mark"></span><h2>Gym Description</h2></div>
  <p class="copy copy-tight abs" style="left:100px;top:96px;width:460px">Accusantium doloremque laudantium, totam rem aperiam, eaque ipsa quae ab illo inventore veritatis et quasi architecto beatae vitae dicta sunt explicabo. Nemo enim ipsam voluptatem quia voluptas sit aspernatur aut odit aut fugit, sed quia consequuntur magni dolores eos qui ratione voluptatem sequi nesciunt. Neque porro quisquam est, qui dolorem ipsum quia dolor sit amet, consectetur, adipisci velit, sed quia non numquam eius modi tempora incidunt ut labore.</p>
  <a class="btn abs" style="left:100px;top:241px;width:124px;height:45px">Read More</a>
</section>
<div class="photo-hall abs" role="img" aria-label="Open gym hall with calisthenics rigs and bars"></div>

<section class="video">
  <div class="thumb t1 abs" role="img" aria-label="Gymnastic rings hanging in the gym"></div>
  <div class="thumb t2 abs" role="img" aria-label="Athlete stretching"></div>
  <div class="thumb t3 abs" role="img" aria-label="Athlete doing a floor exercise"></div>
  <div class="thumb t4 abs" role="img" aria-label="Athlete training in an open hall"></div>
  <div class="thumb t-main abs" role="img" aria-label="Video still of an athlete on a red pull-up frame"></div>
  <div class="play abs"><svg width="22" height="24" viewBox="0 0 22 24"><path d="M2 1l19 11L2 23z" fill="#fff"/></svg></div>
  <div class="section-head abs" style="left:657px;top:1548px"><span class="section-mark"></span><h2>Watch a Video</h2></div>
  <p class="copy copy-tight abs" style="left:657px;top:1626px;width:440px">Denouncing pleasure and praising the pain was born and I will give you a complete account of the system, and expound the actual teachings of the great explorer of the truth, the master-builder of human happiness. No one rejects, dislikes, or avoids pleasure itself, because it is pleasure, but because those who do not know how to pursue pleasure rationally encounter consequences that are extremely painful. Nor again is there anyone who loves or pursues or desires to obtain pain of itself, because it is pain, but because occasionally circumstances occur in which toil and pain can procure him some great pleasure.</p>
  <a class="btn abs" style="left:657px;top:1818px;width:122px;height:44px">Read More</a>
</section>

<section class="workout abs">
  <div class="workout-photo abs" role="img" aria-label="Athlete in a white sports top against a dark blurred background"></div>
  <div class="section-head abs" style="left:100px;top:66px"><span class="section-mark"></span><h2>Calisthenics workout</h2></div>
  <p class="workout-lead abs">Perspiciatis unde omnis iste natus error sit voluptatem accusantium doloremque laudantium, totam rem aperiam, eaque inventore veritatis et quasi architecto beatae vitae dicta sunt explicabo.</p>

  <div class="feature-icon abs" style="left:100px;top:234px"><svg viewBox="0 0 46 46"><path d="M9 20a15 15 0 0127-7M37 26a15 15 0 01-27 7"/><path d="M36 5v8h-8M10 41v-8h8"/></svg></div>
  <div class="feature abs" style="left:164px;top:246px"><h3>Many desktop publishing</h3><p>Passage of Lorem Ipsum, you need to be sure there isn't anything embarrassing hidden in the middle of text. All the Lorem Ipsum generators on the.</p></div>

  <div class="feature-icon abs" style="left:497px;top:234px"><svg viewBox="0 0 46 46"><circle cx="28" cy="7" r="4"/><path d="M26 13l-6 12 8 6-4 12M20 25l-10 4M24 17l10 6"/></svg></div>
  <div class="feature abs" style="left:558px;top:246px"><h3>Neque porro quisquam est</h3><p>Passage of Lorem Ipsum, you need to be sure there isn't anything embarrassing hidden in the middle of text. All the Lorem Ipsum generators on the.</p></div>

  <div class="feature-icon abs" style="left:100px;top:364px"><svg viewBox="0 0 46 46"><circle cx="14" cy="8" r="4"/><path d="M14 14v16h20M14 22l12-8M4 40h38"/></svg></div>
  <div class="feature abs" style="left:164px;top:376px"><h3>Architecto beatae vitae dicta</h3><p>Passage of Lorem Ipsum, you need to be sure there isn't anything embarrassing hidden in the middle of text. All the Lorem Ipsum generators on the.</p></div>

  <div class="feature-icon abs" style="left:497px;top:364px"><svg viewBox="0 0 46 46"><circle cx="23" cy="25" r="16"/><path d="M23 9V4M17 22l6 6 6-6"/></svg></div>
  <div class="feature abs" style="left:558px;top:376px"><h3>Lorem Ipsum is not simply</h3><p>Passage of Lorem Ipsum, you need to be sure there isn't anything embarrassing hidden in the middle of text. All the Lorem Ipsum generators on the.</p></div>
</section>

<section class="cta">
  <h2 class="cta-title abs">LOREM IPSUM DOLOR SIT AMET, CONSECTETUR ADIPISCING ELIT</h2>
  <p class="cta-copy abs">voluptatem accusantium doloremque laudantium, totam rem aperiam, eaque ipsa quae ab illo inventore veritatis et quasi architecto beatae vitae dicta sunt explicabo. Nemo enim ipsam voluptatem quia voluptas sit aspern</p>
  <a class="cta-btn abs"><strong>GET START TODAY</strong><span>Your first session is free</span></a>
</section>

<footer class="site-footer abs">
  <div class="foot-head abs" style="left:100px;top:45px">Summit Gym</div>
  <ul class="foot-list abs" style="left:100px;top:80px">
    <li>Home</li><li>Class descriptions</li><li>Gym description</li><li>Class schedules</li><li>Trainer profiles</li><li>Gym philosophy</li>
  </ul>

  <div class="foot-head abs" style="left:392px;top:45px">Contact Us</div>
  <ul class="foot-list foot-contact abs" style="left:392px;top:80px">
    <li><svg viewBox="0 0 14 14"><path d="M0 2h14v10H0zM1 3l6 5 6-5" fill-rule="evenodd"/></svg>INFO@SUMMITBODYFORM.COM</li>
    <li><svg viewBox="0 0 14 14"><path d="M3 0h3l1 4-2 1a8 8 0 004 4l1-2 4 1v3c0 1-1 2-2 2A12 12 0 011 2c0-1 1-2 2-2z"/></svg>800 555 019</li>
    <li><svg viewBox="0 0 14 14"><path d="M3 0h3l1 4-2 1a8 8 0 004 4l1-2 4 1v3c0 1-1 2-2 2A12 12 0 011 2c0-1 1-2 2-2z"/></svg>+ 971 555 0198</li>
  </ul>
  <div class="socials abs" style="left:392px;top:154px"><span></span><span></span><span></span></div>

  <div class="foot-head abs" style="left:680px;top:45px">About Us</div>
  <p class="about-copy abs" style="left:680px;top:72px">the world's largest professional network with 300 million members in over 200 countries and territories around the globe.</p>
  <div class="foot-head abs" style="left:680px;top:124px">Subscribe to our newsletter</div>
  <div class="newsletter abs"><div class="newsletter-field">Email Address</div><div class="newsletter-btn">Submet</div></div>

  <div class="copyright abs">@ Copyright 2013 Summit .com - all rights reserved</div>
</footer>

</body>
</html>
```